Business cards to launch an education platform

Hi,
I am looking at having new business cards designed.
I am a startup, developing a web platform for schools and university, the education world. It's an online assessment system.
I would like a card that looks classy, and that is using the colors and the font of my logo.

I have attached:
1) my logo
2) A business card that I have designed quickly so you can have all the information required in the card, but I really don't like it.
3) The font that I am using (Lato Regular) to design my web platform
4) Some screenshots of my web platform so you can have a look at the style that I have.

Target Market(s)

Major market: Education system: Schools and university
Minor markets: Business in general

Industry/Entity Type

Business

Contact Information for Business Card

Clara Fenwick
Director

M: 0437 518 902
E: clara.fenwick@amberLoomSystems.com.au

Requirements
Must have
• The colors of my logo

```html
<!DOCTYPE html>
<html lang="en">
<head>
<meta charset="utf-8">
<title>Amber Loom Systems – Business Card</title>
<link rel="stylesheet" href="https://fonts.googleapis.com/css2?family=Lato:wght@400;700&display=swap">
<style>
  :root {
    --backdrop: #e9e6e1;
    --card-black: #0c0d0f;
    --card-white: #f7f8f8;
    --brand-blue: #3aa6d6;
    --stripe-blue: #8fd4e6;
    --ink: #1b1b1b;
  }
  * { box-sizing: border-box; margin: 0; padding: 0; }
  html, body { width: 1200px; height: 892px; overflow: hidden; }
  body {
    background: var(--backdrop);
    font-family: "Lato", sans-serif;
    position: relative;
  }
  .card {
    position: absolute;
    top: 287px;
    width: 520px;
    height: 318px;
    border-radius: 18px;
    overflow: hidden;
    box-shadow: 0 10px 28px rgba(0,0,0,0.28);
  }
  .card--front { left: 50px; background: var(--card-white); }
  .card--back { left: 630px; background: var(--card-black); }
  .card__shape { position: absolute; inset: 0; }

  .brand {
    position: absolute;
    display: flex;
    align-items: center;
    gap: 12px;
    color: var(--brand-blue);
    font-weight: 400;
    letter-spacing: 0.08em;
    text-transform: uppercase;
    white-space: nowrap;
  }
  .brand__mark { background: var(--brand-blue); flex: none; }
  .brand__name { display: flex; flex-direction: column; line-height: 1.15; }
  .card--front .brand { left: 30px; top: 34px; font-size: 19px; }
  .card--front .brand__mark { width: 40px; height: 40px; }
  .card--back .brand {
    left: 50%; top: 50%;
    transform: translate(-50%, -50%);
    font-size: 26px;
  }
  .card--back .brand__mark { width: 42px; height: 42px; }

  .contact-line {
    position: absolute;
    right: 26px;
    display: flex;
    align-items: center;
    gap: 8px;
    font-size: 14px;
    color: var(--ink);
  }
  .contact-line--phone { top: 36px; font-size: 17px; }
  .contact-line--email { top: 150px; }
  .contact-icon {
    width: 16px; height: 16px;
    background: var(--brand-blue);
    border-radius: 2px;
    display: flex; align-items: center; justify-content: center;
  }
  .person { position: absolute; left: 56px; top: 236px; }
  .person__name {
    font-size: 36px;
    font-weight: 400;
    color: var(--brand-blue);
    line-height: 1.05;
  }
  .person__role { font-size: 17px; color: var(--ink); margin-top: 2px; }
</style>
</head>
<body>
  <section class="card card--front" aria-label="Business card front">
    <svg class="card__shape" viewBox="0 0 520 318" aria-hidden="true">
      <path d="M0 0 H360 C300 40 240 170 0 262 V318 H0 Z" fill="var(--stripe-blue)"/>
      <path d="M0 0 H346 C288 36 226 162 0 248 Z" fill="var(--card-white)"/>
      <path d="M0 0 H334 C276 30 214 152 0 236 Z" fill="var(--card-black)"/>
    </svg>
    <div class="brand">
      <span class="brand__mark"></span>
      <span class="brand__name"><span>Amber Loom</span><span>Systems</span></span>
    </div>
    <div class="contact-line contact-line--phone">
      0437 518 902
      <span class="contact-icon">
        <svg width="10" height="10" viewBox="0 0 10 10" aria-hidden="true"><path d="M2 1 L4 3 L3 4 Q4 6 6 7 L7 6 L9 8 L8 9 Q4 9 1 5 Q1 2 2 1 Z" fill="#fff"/></svg>
      </span>
    </div>
    <div class="contact-line contact-line--email">
      clara.fenwick@amberLoomSystems.com.au
      <span class="contact-icon">
        <svg width="10" height="8" viewBox="0 0 10 8" aria-hidden="true"><rect x="0.5" y="0.5" width="9" height="7" fill="none" stroke="#fff"/><path d="M0.5 0.5 L5 4.5 L9.5 0.5" fill="none" stroke="#fff"/></svg>
      </span>
    </div>
    <div class="person">
      <h1 class="person__name">Clara Fenwick</h1>
      <p class="person__role">Director</p>
    </div>
  </section>

  <section class="card card--back" aria-label="Business card back">
    <div class="brand">
      <span class="brand__mark"></span>
      <span class="brand__name"><span>Amber Loom</span><span>Systems</span></span>
    </div>
  </section>
</body>
</html>
```